BVM Marketing Postcard

Design a 2 Sided marketing postcard for our Real estate management caompany. Looking for a professional yet fresh look that will be printed on a 6"x9" glossy flier

Contact information is www.brixleymanagement.example brixleymanagement@postwellmail.example and 555-014-7283

WE are targeting small condo and town home properties to take on their administrative responsibilities of management

```html
<!DOCTYPE html>
<html lang="en">
<head>
<meta charset="utf-8">
<title>BVM Marketing Postcard</title>
<link rel="stylesheet" href="https://fonts.googleapis.com/css2?family=Source+Sans+3:wght@400;600&display=swap">
<style>
:root{
  --navy:#3b4a66;
  --navy-deep:#2f3d57;
  --steel:#8fa3b8;
  --ice:#dbe7f2;
  --ink:#4d4f55;
  --paper:#ffffff;
  --backdrop:#e9ebee;
}
*{box-sizing:border-box;margin:0;padding:0}
html,body{width:913px;height:1200px;overflow:hidden;background:var(--backdrop);font-family:"Source Sans 3",sans-serif;color:var(--ink)}
.card{position:absolute;left:72px;width:768px;height:510px;background:var(--paper);overflow:hidden;box-shadow:0 2px 6px rgba(0,0,0,.18)}
.card--front{top:43px}
.card--back{top:609px}
.brand{position:absolute;left:20px;top:28px;display:flex;align-items:baseline;gap:10px;color:var(--navy)}
.brand__mark{font-size:29px;font-weight:600;letter-spacing:1px}
.brand__name{font-size:17px;font-weight:400;letter-spacing:-.2px}
.headline-band{position:absolute;left:0;top:68px;width:437px;height:77px;background:var(--navy);color:#fff;font-size:17.5px;line-height:21px;padding:15px 20px}
.hero-art{position:absolute;left:0;top:0}
.section{position:absolute;left:20px;font-size:11.5px;line-height:14.2px}
.section h2{font-size:13px;font-weight:600;color:var(--navy);margin-bottom:3px}
.section p{margin:0;white-space:nowrap}
.section--who{top:162px}
.section--why{top:250px}
.section--what{top:340px}
.checklist{list-style:none}
.checklist li{position:relative;padding-left:12px;line-height:15.3px;white-space:nowrap}
.checklist li::before{content:"";position:absolute;left:0;top:4.5px;width:7px;height:7px;border-radius:50%;background:var(--steel)}
.checklist .fine{font-size:8.5px}
.url-pill{position:absolute;left:478px;top:462px;width:268px;height:30px;border-radius:12px;background:var(--navy);color:#fff;font-size:15px;font-weight:600;display:flex;align-items:center;justify-content:center;letter-spacing:.2px}
.edge-stripe{position:absolute;left:0;bottom:0;width:100%;height:11px;display:flex}
.edge-stripe span:first-child{flex:0 0 384px;background:var(--navy)}
.edge-stripe span:last-child{flex:1;background:var(--steel)}
.photo-band{position:absolute;left:0;top:69px;width:100%;height:165px;background:linear-gradient(90deg,#dcdedd 0%,#eeeeec 45%,#e4e3df 75%,#d3d5d8 100%)}
.benefits-panel{position:absolute;left:0;top:238px;width:100%;height:212px;background:linear-gradient(180deg,#3e4d68 0%,#34425c 100%);padding:14px 0 0 36px}
.benefits{list-style:none;color:#fff;font-size:14.5px}
.benefits li{position:relative;padding-left:16px;height:23.8px;line-height:20px}
.benefits li::before{content:"";position:absolute;left:0;top:6px;width:8px;height:8px;border-radius:50%;background:var(--ice)}
.phone-pill{position:absolute;left:250px;top:434px;width:268px;height:33px;border-radius:12px;background:var(--steel);color:#fff;font-size:24px;display:flex;align-items:center;justify-content:center;gap:12px;letter-spacing:.5px}
.back-url{position:absolute;left:0;width:100%;top:471px;text-align:center;font-size:17px;font-weight:600;color:var(--navy)}
</style>
</head>
<body>

<section class="card card--front">
  <svg class="hero-art" width="768" height="510" viewBox="0 0 768 510">
    <defs>
      <linearGradient id="brownstone" x1="0" y1="0" x2="1" y2="1">
        <stop offset="0" stop-color="#7a5446"/>
        <stop offset=".55" stop-color="#5e3f36"/>
        <stop offset="1" stop-color="#8c8580"/>
      </linearGradient>
      <linearGradient id="meeting" x1="0" y1="0" x2="1" y2="1">
        <stop offset="0" stop-color="#e9eef3"/>
        <stop offset="1" stop-color="#9fb3c9"/>
      </linearGradient>
    </defs>
    <circle cx="645" cy="185" r="200" fill="none" stroke="var(--steel)" stroke-width="14"/>
    <circle cx="645" cy="185" r="190" fill="url(#brownstone)" role="img" aria-label="Photo of a row of brownstone townhouses"/>
    <circle cx="517" cy="320" r="78" fill="var(--ice)"/>
    <circle cx="517" cy="320" r="68" fill="url(#meeting)" role="img" aria-label="Photo of a smiling couple meeting with an advisor"/>
  </svg>

  <header class="brand">
    <span class="brand__mark">BVM</span>
    <span class="brand__name">BRIXLEY PROPERTY MANAGEMENT LLC</span>
  </header>

  <div class="headline-band">Improve compliance, reporting, and communication amongst all owners and board members</div>

  <div class="section section--who">
    <h2>Who we are:</h2>
    <p>• A professional services organization with a focus on small (3-10 unit)</p>
    <p>residential buildings</p>
    <p>• Over 30 years of combined experience in real estate and property management</p>
    <p>• Professional, courteous, timely service that is technologically driven</p>
  </div>

  <div class="section section--why">
    <h2>Why use BVM?</h2>
    <p>• Owners are rarely suited to manage associations and the burden often falls unfairly</p>
    <p>on one or two individuals to do all the work</p>
    <p>• Low monthly fees tailored to your needs</p>
    <p>• The association’s board of directors maintains control of all decision making</p>
  </div>

  <div class="section section--what">
    <h2>What we do:</h2>
    <ul class="checklist">
      <li>Remove the administrative burden of managing small residential buildings</li>
      <li>Utilize economies of scale to reduce expenses for all owners across a wide variety<br>of service providers</li>
      <li>Collect all assessments and pay all bills</li>
      <li>Provide monthly accounting reconciliation and reporting</li>
      <li>Provide access to BVM’s client portal with a central repository of all association materials <span class="fine">(bylaws, financials, meeting minutes, communications, etc)</span></li>
      <li>Issue 1099s to all contractors as required by law</li>
      <li>Prepare year-end financial statements</li>
      <li>Lender and legal HOA documents for mortgage companies and sales</li>
    </ul>
  </div>

  <div class="url-pill">www.brixleymanagement.example</div>
  <div class="edge-stripe"><span></span><span></span></div>
</section>

<section class="card card--back">
  <header class="brand">
    <span class="brand__mark">BVM</span>
    <span class="brand__name">BRIXLEY PROPERTY MANAGEMENT LLC</span>
  </header>

  <div class="photo-band" role="img" aria-label="Photo of a handshake beside a small house model and a hand passing a set of keys"></div>

  <div class="benefits-panel" role="img" aria-label="Faded photo of an apartment building behind the list">
    <ul class="benefits">
      <li>Cost effective property management solution for 3-10 unit buildings</li>
      <li>Prices starting as low as $100/month</li>
      <li>Utilize our economies of scale to reduce costs across existing services (trash, insurance, maintenance, etc)</li>
      <li>Eliminate the unfair burden placed on a few owners to do all the work while others free-ride</li>
      <li>Improve communication amongst all owners and board members</li>
      <li>The association’s board of directors maintain all decision-making power</li>
      <li>Utilize our vetted service providers for prompt job completion and fair pricing</li>
    </ul>
  </div>

  <div class="phone-pill">
    <svg width="24" height="24" viewBox="0 0 24 24" aria-hidden="true">
      <circle cx="12" cy="12" r="10.5" fill="none" stroke="#fff" stroke-width="1.6"/>
      <path d="M8.6 6.8l1.6-.4 1.2 2.6-1 1c.6 1.3 1.5 2.2 2.8 2.8l1-1 2.6 1.2-.4 1.6c-.2.6-.8 1-1.5.9-3.5-.5-6.3-3.3-6.8-6.8-.1-.7.3-1.3.5-1.9z" fill="#fff"/>
    </svg>
    <span>555-014-7283</span>
  </div>
  <div class="back-url">www.brixleymanagement.example</div>
  <div class="edge-stripe"><span></span><span></span></div>
</section>

</body>
</html>
```